Logo, Web and Mobile Designs for enterprise social media platform

All the details are in the attached document, please start reading the scope document first which explains what is this project about and the details about the needed deliverables, after that please read the UI_Requirements document which will detail what is expected regarding the coded web version since this is a coded contest, it is very important that you meet the UI requirements or suggest something else but we will need to agree first before working on the coded version

Good Luck

Target Market(s)

Enterprise Social Media

Industry/Entity Type

Media

Coding

Coded - Design and coding required

Number of Pages Required

5+ page

Font styles to use
Sans Serif

Requirements
Must have
• All the must haves are listed in the scope document so please check before you start

```html
<!DOCTYPE html>
<html lang="en">
<head>
<meta charset="utf-8">
<title>Teamora – Profile</title>
<link href="https://fonts.googleapis.com/css2?family=Lato:wght@400;700&display=swap" rel="stylesheet">
<style>
:root{
  --navy:#1f2230;
  --blue:#1aa6e0;
  --grey-btn:#3a3f50;
  --link:#3b5998;
  --text:#222;
  --muted:#8a8f99;
  --line:#e3e5e8;
  --panel:#f2f3f5;
  --green:#2bb24c;
  --tab-grey:#a6b1bb;
}
*{box-sizing:border-box;margin:0;padding:0}
html,body{width:884px;height:1200px;overflow:hidden;background:#fff;font-family:'Lato',Arial,sans-serif;color:var(--text)}
.abs{position:absolute}
.site-header{position:absolute;left:0;top:0;width:884px;height:66px;background:var(--navy)}
.brand{position:absolute;left:72px;top:20px;color:#fff;font-size:22px}
.btn{position:absolute;top:21px;height:23px;width:73px;color:#fff;font-size:11px;display:flex;align-items:center;justify-content:center}
.btn-login{left:662px;background:var(--blue)}
.btn-register{left:738px;background:var(--grey-btn)}
.photo{position:absolute}
.cover{left:74px;top:101px;width:536px;height:225px;background:linear-gradient(135deg,#f4eef0,#e7ecef 55%,#f1ece4)}
.avatar-lg{left:82px;top:212px;width:106px;height:106px;background:linear-gradient(#4d6070,#2f3a44);border:2px solid #fff}
.profile-name{left:196px;top:256px;font-size:15px;font-weight:700;color:#111}
.profile-sub{left:196px;top:278px;font-size:10px;color:#111}
.tabs{left:198px;top:307px;display:flex;gap:21px;font-size:9px;color:#222}
.tabs .on{font-weight:700;border-bottom:2px solid #333;padding-bottom:1px}
.box{position:absolute;border:1px solid var(--line);background:#fff}
.sec-head{position:absolute;background:var(--panel);font-size:7.5px;font-weight:700;color:#444;display:flex;align-items:center;justify-content:space-between;padding:0 8px}
.small{font-size:8.5px;line-height:11.5px}
.link{color:var(--link)}
.friend-row{position:absolute;left:74px;width:206px;height:54px;border-bottom:1px solid var(--line)}
.friend-row .pic{position:absolute;left:4px;top:3px;width:70px;height:48px}
.friend-row span{position:absolute;left:82px;top:22px;font-size:7.5px;font-weight:700}
.grid-ph{position:absolute;width:65px;height:65px}
.post{position:absolute;left:287px;width:323px;border:1px solid var(--line);background:#fff}
.post .av{position:absolute;left:8px;top:8px;width:24px;height:24px}
.post .who{position:absolute;left:40px;top:10px;font-size:7.5px;color:#555}
.post .who b{color:var(--link)}
.post .when{position:absolute;left:40px;top:21px;font-size:7.5px;color:#666}
.post .body{position:absolute;left:8px;width:305px;font-size:7.5px;line-height:11px}
.post .acts{position:absolute;left:0;bottom:0;width:100%;height:20px;background:var(--panel);border-top:1px solid var(--line);font-size:7.5px;color:var(--link);padding:6px 8px}
.side-title{position:absolute;font-size:12px;color:#222}
.chat{position:absolute;left:640px;width:171px;height:31px;border-bottom:1px solid var(--line);font-size:8px;color:var(--muted);padding-top:10px}
.chat svg{position:absolute;right:0;top:10px}
.news{position:absolute;left:641px;width:170px;height:68px;border-bottom:1px solid var(--line)}
.news .th{position:absolute;left:0;top:0;width:62px;height:50px}
.news .dt{position:absolute;left:72px;top:0;font-size:7px;color:var(--muted)}
.news .ct{position:absolute;right:0;top:0;font-size:7px;color:var(--muted)}
.news .tt{position:absolute;left:72px;top:14px;font-size:8.5px;line-height:15px;color:#333}
.footer{position:absolute;left:0;top:1148px;width:884px;height:52px;background:#000;color:#aaa;font-size:8.5px;display:flex;align-items:center;justify-content:center}
</style>
</head>
<body>

<header class="site-header">
  <div class="brand">Teamora</div>
  <div class="btn btn-login">LOGIN</div>
  <div class="btn btn-register">REGISTER</div>
</header>

<!-- profile cover -->
<div class="photo cover" role="img" aria-label="Cover photo of a bright shelf with books and a desk lamp"></div>
<div class="photo avatar-lg" role="img" aria-label="Profile photo"></div>
<div class="abs profile-name">Jhone Doe</div>
<div class="abs profile-sub">Website</div>
<nav class="abs tabs"><span class="on">Timeline</span><span>About</span><span>Welcome</span><span>FWB</span><span>More ▾</span></nav>

<!-- left column -->
<div class="box" style="left:74px;top:350px;width:206px;height:86px">
  <div class="abs" style="left:8px;top:6px;font-size:9.5px;font-weight:700">About Your page name</div>
  <div class="abs small link" style="left:8px;top:19px;width:190px">Lorem ipsum dolor sit amet timeti ergo sum Lorem ipsum dolor sit amet timeti dolor sit amet timeti</div>
  <div class="abs" style="left:0;top:60px;width:204px;border-top:1px solid var(--line)"></div>
  <div class="abs link" style="left:8px;top:67px;font-size:9px;font-weight:700"><span style="color:#aaa;font-weight:400">⊕</span> your website</div>
</div>
<div class="sec-head" style="left:74px;top:442px;width:206px;height:24px"><span>ABOUT</span><span style="color:#aaa">›</span></div>
<div class="box" style="left:74px;top:466px;width:206px;height:65px;border-top:none">
  <svg class="abs" style="left:8px;top:9px" width="7" height="9" viewBox="0 0 7 9"><path d="M3.5 0a3.5 3.5 0 0 0-3.5 3.5C0 6 3.5 9 3.5 9S7 6 7 3.5A3.5 3.5 0 0 0 3.5 0zm0 5a1.4 1.4 0 1 1 0-2.8 1.4 1.4 0 0 1 0 2.8z" fill="#555"/></svg>
  <div class="abs" style="left:21px;top:7px;font-size:9px;color:#333;line-height:11px">Your Adress<br><span style="color:#888">City, Country</span></div>
  <div class="abs" style="left:8px;top:38px;width:190px;border-top:1px solid var(--line)"></div>
  <svg class="abs" style="left:8px;top:47px" width="8" height="8" viewBox="0 0 8 8"><path d="M1.5 0l1.6 1.7-.8 1.2c.5 1 1.4 1.9 2.4 2.4l1.2-.8L8 6.5 6.8 8C3.2 7.6.4 4.8 0 1.2z" fill="#555"/></svg>
  <div class="abs link" style="left:21px;top:44px;font-size:9px;font-weight:700">Add phone number</div>
</div>
<div class="sec-head" style="left:74px;top:539px;width:206px;height:23px"><span>Friends</span><span>162</span></div>
<div class="friend-row" style="top:562px"><div class="photo pic" role="img" aria-label="Friend photo" style="background:#c99a72"></div><span>Jhone Doe</span></div>
<div class="friend-row" style="top:618px"><div class="photo pic" role="img" aria-label="Friend photo" style="background:#9c9892"></div><span>Richerds</span></div>
<div class="friend-row" style="top:674px"><div class="photo pic" role="img" aria-label="Friend photo" style="background:#b8aca2"></div><span>Oren Vale</span></div>
<div class="sec-head" style="left:74px;top:738px;width:206px;height:23px"><span>PHOTOS</span><span style="color:#aaa">›</span></div>
<div class="grid-ph" role="img" aria-label="Office meeting photo" style="left:76px;top:763px;background:#6d7480"></div>
<div class="grid-ph" role="img" aria-label="Kitchen team photo" style="left:144px;top:763px;background:#a49a8c"></div>
<div class="grid-ph" role="img" aria-label="Handshake photo" style="left:213px;top:763px;background:#506070"></div>
<div class="grid-ph" role="img" aria-label="Business card photo" style="left:76px;top:832px;background:#4a4e58"></div>
<div class="grid-ph" role="img" aria-label="Shop counter photo" style="left:144px;top:832px;background:#8a8272"></div>
<div class="grid-ph" role="img" aria-label="City skyline photo" style="left:213px;top:832px;background:#8a9098"></div>
<div class="grid-ph" role="img" aria-label="Desk from above photo" style="left:76px;top:901px;background:#8c6a48"></div>

<!-- feed -->
<article class="post" style="top:334px;height:182px">
  <div class="photo av" role="img" aria-label="Page avatar" style="background:#a08070"></div>
  <div class="who"><b>Your page name</b> changed their <span class="link">cover photo.</span></div>
  <div class="when">3 minutes ago ◍</div>
  <div class="photo" role="img" aria-label="Team meeting photo" style="left:2px;top:42px;width:318px;height:118px;background:linear-gradient(90deg,#9fb0bf,#5d6a78 60%,#c5ccd2)"></div>
  <div class="acts">Like · Comment · Share</div>
</article>
<article class="post" style="top:524px;height:104px">
  <div class="photo av" role="img" aria-label="Page avatar" style="background:#6a7078"></div>
  <div class="who"><b>Your page name</b></div>
  <div class="when">December 12, 2013 ◍</div>
  <div class="body" style="top:49px">Lorem ipsum dolor sit amet timeti ergo sum Lorem ipsum dolor sit amet timeti dolor sit amet timeti imeti ergo sum imeti ergo sum</div>
  <div class="acts">Like · Comment · Share</div>
</article>
<article class="post" style="top:636px;height:230px">
  <div class="photo av" role="img" aria-label="Page avatar" style="background:#b07a60"></div>
  <div class="who"><b>Your page name</b> created an event.</div>
  <div class="when">september 3, 3013 ◍</div>
  <div class="photo" role="img" aria-label="Tablet showing charts" style="left:9px;top:42px;width:306px;height:114px;background:linear-gradient(135deg,#b8c2c8,#dfe8ef 50%,#8c9aa4)"></div>
  <div class="abs" style="left:9px;top:156px;width:306px;height:40px;background:#f7f8f9;border:1px solid var(--line)"></div>
  <div class="abs" style="left:16px;top:161px;font-size:7.5px;line-height:9.5px;color:#666"><b class="link">Event name</b><br>Tuesday, September 3, 2013 at 6:00pm<br>Adress, City, Country, 1051</div>
  <div class="abs" style="left:272px;top:175px;width:35px;height:13px;border:1px solid #aaa;background:#fff;font-size:7px;font-weight:700;text-align:center;line-height:11px">▭ Join</div>
  <div class="acts">Like · Comment · Get Notifications · Share</div>
</article>
<article class="post" style="top:874px;height:104px">
  <div class="photo av" role="img" aria-label="Page avatar" style="background:#c8a070"></div>
  <div class="who"><b>Your page name</b></div>
  <div class="when">December 12, 2013 ◍</div>
  <div class="body" style="top:49px">Lorem ipsum dolor sit amet timeti ergo sum Lorem ipsum dolor sit amet timeti dolor sit amet timeti imeti ergo sum imeti ergo sum</div>
  <div class="acts">Like · Comment · Share</div>
</article>
<article class="post" style="top:994px;height:104px">
  <div class="photo av" role="img" aria-label="Page avatar" style="background:#a06858"></div>
  <div class="who"><b>Your page name</b></div>
  <div class="when">December 12, 2013 ◍</div>
  <div class="body" style="top:49px">Lorem ipsum dolor sit amet timeti ergo sum Lorem ipsum dolor sit amet timeti dolor sit amet timeti imeti ergo sum imeti ergo sum</div>
  <div class="acts">Like · Comment · Share</div>
</article>

<!-- right column -->
<div class="side-title" style="left:642px;top:97px">Chat Friends</div>
<div class="chat" style="top:121px">Jhone doe<svg width="9" height="8" viewBox="0 0 9 8"><path d="M4.5 0C2 0 0 1.5 0 3.4c0 1 .6 1.9 1.5 2.5L1 8l2.3-1.3c.4.1.8.1 1.2.1C7 6.8 9 5.3 9 3.4S7 0 4.5 0z" fill="var(--green)"/></svg></div>
<div class="chat" style="top:152px">Richerds elementum<svg width="9" height="8" viewBox="0 0 9 8"><path d="M4.5 0C2 0 0 1.5 0 3.4c0 1 .6 1.9 1.5 2.5L1 8l2.3-1.3c.4.1.8.1 1.2.1C7 6.8 9 5.3 9 3.4S7 0 4.5 0z" fill="var(--green)"/></svg></div>
<div class="chat" style="top:184px">lacinia. Fusce tincidunt<svg width="9" height="8" viewBox="0 0 9 8"><path d="M4.5 0C2 0 0 1.5 0 3.4c0 1 .6 1.9 1.5 2.5L1 8l2.3-1.3c.4.1.8.1 1.2.1C7 6.8 9 5.3 9 3.4S7 0 4.5 0z" fill="var(--green)"/></svg></div>
<div class="chat" style="top:216px">turpis at augue<svg width="9" height="8" viewBox="0 0 9 8"><path d="M4.5 0C2 0 0 1.5 0 3.4c0 1 .6 1.9 1.5 2.5L1 8l2.3-1.3c.4.1.8.1 1.2.1C7 6.8 9 5.3 9 3.4S7 0 4.5 0z" fill="var(--green)"/></svg></div>
<div class="chat" style="top:247px">tincidunt,<svg width="9" height="8" viewBox="0 0 9 8"><path d="M4.5 0C2 0 0 1.5 0 3.4c0 1 .6 1.9 1.5 2.5L1 8l2.3-1.3c.4.1.8.1 1.2.1C7 6.8 9 5.3 9 3.4S7 0 4.5 0z" fill="var(--green)"/></svg></div>
<div class="chat" style="top:279px">a sagittis elit dictum.<svg width="9" height="8" viewBox="0 0 9 8"><path d="M4.5 0C2 0 0 1.5 0 3.4c0 1 .6 1.9 1.5 2.5L1 8l2.3-1.3c.4.1.8.1 1.2.1C7 6.8 9 5.3 9 3.4S7 0 4.5 0z" fill="var(--green)"/></svg></div>
<div class="chat" style="top:310px">Ut porttitor,<svg width="9" height="8" viewBox="0 0 9 8"><path d="M4.5 0C2 0 0 1.5 0 3.4c0 1 .6 1.9 1.5 2.5L1 8l2.3-1.3c.4.1.8.1 1.2.1C7 6.8 9 5.3 9 3.4S7 0 4.5 0z" fill="var(--green)"/></svg></div>
<div class="chat" style="top:342px">ex a sagittis malesuada<svg width="9" height="8" viewBox="0 0 9 8"><path d="M4.5 0C2 0 0 1.5 0 3.4c0 1 .6 1.9 1.5 2.5L1 8l2.3-1.3c.4.1.8.1 1.2.1C7 6.8 9 5.3 9 3.4S7 0 4.5 0z" fill="var(--green)"/></svg></div>

<div class="side-title" style="left:638px;top:416px">Events &amp; News</div>
<div class="abs" style="left:641px;top:446px;width:86px;height:32px;background:var(--navy);border-top:2px solid var(--blue);color:#fff;font-size:8.5px;display:flex;align-items:center;justify-content:center">Recent Post</div>
<div class="abs" style="left:727px;top:448px;width:84px;height:30px;background:var(--tab-grey);color:#fff;font-size:8.5px;display:flex;align-items:center;justify-content:center">Popular Events</div>

<div class="news" style="top:497px"><div class="photo th" role="img" aria-label="News photo" style="background:#7a6e78"></div><div class="dt">July 27, 2014</div><div class="ct">🗨 3</div><div class="tt">30 Photographic Works<br>of Impressive Old Age</div></div>
<div class="news" style="top:573px"><div class="photo th" role="img" aria-label="News photo" style="background:#8aa0b4"></div><div class="dt">July 27, 2014</div><div class="ct">🗨 3</div><div class="tt">30 Photographic Works<br>of Impressive Old Age</div></div>
<div class="news" style="top:649px"><div class="photo th" role="img" aria-label="News photo" style="background:#6e7884"></div><div class="dt">July 27, 2014</div><div class="ct">🗨 3</div><div class="tt">30 Photographic Works<br>of Impressive Old Age</div></div>
<div class="news" style="top:726px"><div class="photo th" role="img" aria-label="News photo" style="background:#b07a48"></div><div class="dt">July 27, 2014</div><div class="ct">🗨 3</div><div class="tt">30 Photographic Works<br>of Impressive Old Age</div></div>
<div class="news" style="top:802px"><div class="photo th" role="img" aria-label="News photo" style="background:#50555e"></div><div class="dt">July 27, 2014</div><div class="ct">🗨 3</div><div class="tt">30 Photographic Works<br>of Impressive Old Age</div></div>

<div class="side-title" style="left:641px;top:882px">Videos</div>
<div class="photo" role="img" aria-label="Video still of a hand on a tablet" style="left:641px;top:913px;width:170px;height:125px;background:linear-gradient(135deg,#3e4a58,#7a8a98 60%,#b0b8c0)"></div>
<svg class="abs" style="left:715px;top:965px" width="22" height="22" viewBox="0 0 22 22"><circle cx="11" cy="11" r="11" fill="#fff"/><path d="M8.5 6.5l7 4.5-7 4.5z" fill="#333"/></svg>
<svg class="abs" style="left:655px;top:1038px" width="12" height="6" viewBox="0 0 12 6"><path d="M0 0h12L6 6z" fill="#7a8a98"/></svg>
<div class="abs" style="left:641px;top:1057px;font-size:8.5px;font-weight:700;color:#333">Lorm Ipsum</div>
<svg class="abs" style="left:780px;top:1059px" width="32" height="6" viewBox="0 0 32 6"><g fill="none" stroke="#9ad" stroke-width=".8"><circle cx="3" cy="3" r="2.3"/><circle cx="11" cy="3" r="2.3"/><circle cx="27" cy="3" r="2.3"/></g><circle cx="19" cy="3" r="2.6" fill="#1aa39a"/></svg>

<footer class="footer">Copyright 2015 yoursite &nbsp;|&nbsp; All Rights Reserved</footer>
</body>
</html>
```